Bramblewood Joinery Website

My client Bramblewood Joinery is looking for a redesign for a Word Press Website. Their current site is at www.bramblewoodjoinery.example They are a custom cabinet company, but also create bathroom, living room, bar and entertainment and bedroom cabinets too. They would like a design that emulates the master craftsman work they do yet a contemporary style.

Their current site was designed using Flash elements.

Target Market(s)

Home owners and builders of high end homes

Industry/Entity Type

Entertainment

Font styles to use
Serif
Decorative

Requirements
Must have
• Must show their work and logo using a contemporary style.
Nice to have
• Sliders that showcase their projects.

```html
<!DOCTYPE html>
<html lang="en">
<head>
<meta charset="utf-8">
<title>Bramblewood Joinery</title>
<link href="https://fonts.googleapis.com/css2?family=Open+Sans:wght@400;600;700&display=swap" rel="stylesheet">
<style>
:root{
  --wood-dark:#6b2a14;
  --wood-mid:#8e3e1d;
  --wood-light:#a34d26;
  --green:#3fae2a;
  --nav:#222;
  --panel:#2b2b2b;
  --footer:#242424;
  --footer-text:#8a8a8a;
  --text:#555;
  --heading:#444;
  --white:#fff;
}
*{margin:0;padding:0;box-sizing:border-box}
html,body{width:821px;height:1200px;overflow:hidden}
body{
  font-family:"Open Sans",sans-serif;
  background:linear-gradient(90deg,var(--wood-dark),var(--wood-light) 30%,var(--wood-mid) 60%,var(--wood-light) 85%,var(--wood-dark));
  position:relative;color:var(--text);
}
.abs{position:absolute}
.page{position:absolute;left:41px;top:10px;width:739px;height:1178px;background:var(--white);border-top:2px solid var(--green)}
.social-square{position:absolute;width:23px;height:23px}
.brand{position:absolute;left:330px;top:18px;width:160px;height:92px;text-align:center}
.brand-dot{width:40px;height:40px;border-radius:50%;background:var(--green);margin:0 auto 6px}
.brand-name{font-size:13px;font-weight:700;color:#1e1e1e;letter-spacing:.5px}
.call{position:absolute;left:652px;top:40px;font-size:15px;color:#444}
.call-number{position:absolute;left:653px;top:64px;font-size:11.5px;color:#444}
.nav{position:absolute;left:50px;top:114px;width:720px;height:31px;background:var(--nav);display:flex}
.nav a{color:var(--white);font-size:9px;text-decoration:none;display:flex;align-items:center;padding:0 14px;border-right:1px solid #333;height:31px}
.nav a.active{background:var(--green);width:70px;justify-content:center;padding:0}
.photo{position:absolute}
.slider{left:50px;top:154px;width:469px;height:312px;background:
  radial-gradient(ellipse 12% 14% at 63% 12%,#f4f6f8,transparent 80%),
  radial-gradient(ellipse 40% 16% at 55% 66%,#d8d2c8,transparent 75%),
  linear-gradient(90deg,#8d8f93 0 13%,transparent 13% 16%),
  linear-gradient(180deg,#5a544d 0,#8a847b 12%,#e2e0dc 30%,#d2cfca 52%,#9a948c 62%,#3a332d 80%,#231e1a 100%)}
.slider-arrow{position:absolute;top:302px;width:18px;height:18px;border-radius:50%;background:rgba(255,255,255,.7)}
.caption{position:absolute;left:68px;top:408px;width:435px;height:42px;background:rgba(63,174,42,.55);color:var(--white);font-size:14px;display:flex;align-items:center;padding-left:20px}
.feature{position:absolute;left:529px;top:154px;width:241px;height:312px;background:var(--panel)}
.feature-photo{left:535px;top:161px;width:228px;height:141px;background:
  linear-gradient(180deg,#c9c5be 0,#8a847c 10%,transparent 12%),
  linear-gradient(90deg,#6d6a66 0 12%,#1a1a1c 12% 88%,#5a5652 88%),
  #1a1a1c}
.feature-title{position:absolute;left:529px;top:313px;width:241px;text-align:center;color:var(--white);font-size:14px}
.feature-text{position:absolute;left:538px;top:336px;width:224px;text-align:center;color:#bbb;font-size:8.8px;line-height:12.2px}
.btn{position:absolute;color:var(--white);font-size:9px;display:flex;align-items:center;justify-content:center}
.btn-dark{background:#3a3a3a;border:1px solid #555}
.btn-green{background:var(--green)}
.section-title{position:absolute;color:var(--heading);font-size:19px}
.intro{position:absolute;left:102px;top:523px;width:616px;text-align:center;font-size:8.8px;line-height:12.8px}
.portfolio{position:absolute;left:50px;top:672px;width:720px;height:216px;border:1px solid #e4e4e4}
.pf-title{position:absolute;left:62px;top:682px;font-size:12px;color:#555}
.pf-title b{color:#333}
.pf-text{position:absolute;left:62px;top:704px;width:510px;font-size:7.8px;line-height:11px}
.thumb{top:763px;width:116px;height:92px}
.dot{position:absolute;top:871px;width:6px;height:6px;border-radius:50%;background:#ddd}
.cat-active{position:absolute;left:588px;top:673px;width:182px;height:18px;background:var(--green);color:var(--white);font-size:9px;padding-left:20px;display:flex;align-items:center}
.cat-list{position:absolute;left:608px;top:692px;list-style:none;font-size:9px;color:#555;line-height:20.5px}
.scroll{position:absolute;left:760px;top:698px;width:4px;height:182px;background:#eee;border-radius:2px}
.scroll i{position:absolute;left:0;top:24px;width:4px;height:32px;background:#999;border-radius:2px}
.cta{position:absolute;left:41px;top:933px;width:739px;height:41px;background:var(--green)}
.cta-text{position:absolute;left:209px;top:942px;color:var(--white);font-size:18px}
.cta-btn{position:absolute;left:419px;top:942px;width:185px;height:24px;border:1.5px solid var(--white);color:var(--white);font-size:11px;font-weight:600;display:flex;align-items:center;justify-content:center}
.footer{position:absolute;left:41px;top:974px;width:739px;height:214px;background:var(--footer)}
.f-head{position:absolute;top:997px;color:#ddd;font-size:8.5px;font-weight:700;letter-spacing:1px}
.f-text{position:absolute;font-size:7.5px;line-height:10.4px;color:var(--footer-text)}
.f-green{color:var(--green)}
.f-links{position:absolute;left:272px;top:1018px;list-style:none;font-size:7.8px;line-height:13.8px;color:#aaa}
.f-field{position:absolute;left:627px;width:142px;height:20px;background:#333;border:1px solid #3c3c3c;color:#777;font-size:6.5px;padding-left:6px;display:flex;align-items:center}
.f-social{position:absolute;top:1106px;width:9px;height:9px;background:#ddd}
.copy{position:absolute;left:41px;top:1160px;width:739px;text-align:center;font-size:7.5px;color:#888}
</style>
</head>
<body>
<div class="page"></div>

<div class="social-square" style="left:51px;top:58px;background:#1d2f7a"></div>
<div class="social-square" style="left:82px;top:58px;background:#888"></div>
<div class="social-square" style="left:114px;top:58px;background:#888"></div>
<div class="social-square" style="left:144px;top:58px;background:#888"></div>

<div class="brand"><div class="brand-dot"></div><div class="brand-name">Bramblewood Joinery</div></div>

<div class="call">Call Us</div>
<div class="call-number">555.014.2300</div>
<svg class="abs" style="left:738px;top:44px" width="28" height="28" viewBox="0 0 24 24"><path d="M6.6 10.8a15 15 0 0 0 6.6 6.6l2.2-2.2c.3-.3.7-.4 1-.2 1.1.4 2.3.6 3.6.6.6 0 1 .4 1 1V20c0 .6-.4 1-1 1C10.6 21 3 13.4 3 4c0-.6.4-1 1-1h3.5c.6 0 1 .4 1 1 0 1.3.2 2.5.6 3.6.1.3 0 .7-.2 1z" fill="#3fae2a"/></svg>

<nav class="nav">
  <a class="active">Home</a><a>Who We Are</a><a>Getting Started</a><a>Contact Us</a><a>Customer Experience</a><a>Professional</a><a>Portfolio</a><a style="border:0">Cabinet Hardware</a>
</nav>

<div class="photo slider" role="img" aria-label="Bright white custom kitchen with range hood, stainless fridge and granite island"></div>
<div class="slider-arrow" style="left:67px"></div>
<div class="slider-arrow" style="left:482px"></div>
<div class="caption">Kansas City's Premier Custom Kitchen Cabinet Design Company</div>

<div class="feature"></div>
<div class="photo feature-photo" role="img" aria-label="Dark stained kitchen island with drawers"></div>
<div class="feature-title">Lorem ipsum dolor sit amet</div>
<div class="feature-text">Nulla facilisi. Pellentesque a sollicitudin lacus, nec placerat diam. Quisque vitae convallis dolor. Duis porttitor libero non gravida facilisis. Mauris non tortor sit amet justo tincidunt ultrices eget at magna. Nunc dictum sem id metus pretium, quis molestie eros mattis.</div>
<div class="btn btn-dark" style="left:563px;top:425px;width:81px;height:18px">Read More</div>
<div class="btn btn-green" style="left:652px;top:425px;width:84px;height:18px">View Works</div>

<div class="section-title" style="left:0;width:821px;text-align:center;top:488px">Who We Are</div>
<p class="intro">Watch Our VideoEstablished in 1966, Bramblewood Joinery has long stood as one of the Midwest's most renowned makers of custom cabinets and fixtures. Our handcrafted, award-winning creations have been chosen by hundreds of noteworthy homebuilders. And while we custom build cabinets, we built our business around the belief that our customers absolutely, unequivocally come first. From day one, our mission has been to help turn the houses that people live in to the homes they've always dreamed of.</p>
<div class="btn btn-green" style="left:331px;top:590px;width:77px;height:20px">Read More</div>
<div class="btn btn-dark" style="left:414px;top:590px;width:76px;height:20px;background:#333">Watch Video</div>

<div class="section-title" style="left:51px;top:639px">Our Portfolio</div>
<div class="portfolio"></div>
<div class="pf-title">Custom <b>Kitchen Cabinets</b> by Bramblewood Joinery</div>
<p class="pf-text">Bramblewood Joinery has been providing kitchens to the Kansas City area for over 40 years. In that time frame we have produced over 55,000 kitchens. Bramblewood is 100% custom and stocks no cabinets. Kitchens are produced from truckloads of rough lumber. We can produce your kitchen in literally any wood type.</p>
<div class="photo thumb" style="left:64px;background:radial-gradient(ellipse 60% 40% at 55% 65%,#5a3a22,transparent 80%),linear-gradient(180deg,#d9b46a 0,#8a5a2c 35%,#4a2a15 70%,#7a4424)" role="img" aria-label="Warm wood kitchen with round island"></div>
<div class="photo thumb" style="left:194px;background:radial-gradient(ellipse 40% 45% at 25% 55%,#6f9a3a,transparent 80%),linear-gradient(160deg,#d2b78a,#6a4a2a 45%,#3a2414)" role="img" aria-label="Carved wood cabinet detail with greenery"></div>
<div class="photo thumb" style="left:323px;background:linear-gradient(180deg,#2a2626 0,#3a3432 35%,#9a948e 55%,#3a3230 70%,#1c1818)" role="img" aria-label="Dark modern kitchen with stainless hood"></div>
<div class="photo thumb" style="left:454px;background:radial-gradient(ellipse 20% 18% at 75% 15%,#f2efe8,transparent 80%),linear-gradient(180deg,#7a3a1c 0,#c9804a 35%,#8a3e1c 65%,#4a1e0e)" role="img" aria-label="Rustic cherry kitchen and dining area"></div>
<span class="dot" style="left:298px;background:var(--green)"></span><span class="dot" style="left:308px"></span><span class="dot" style="left:319px"></span><span class="dot" style="left:329px"></span>

<svg class="abs" style="left:580px;top:676px" width="8" height="12"><path d="M8 0 0 6 8 12z" fill="#3fae2a"/></svg>
<div class="cat-active">Kitchen Cabinets</div>
<ul class="cat-list">
  <li>Kitchen Islands</li><li>Bathroom Cabinets</li><li>Bookcase</li><li>Closets</li><li>Entertainment Centers</li><li>TV Cabinets</li><li>Garage</li><li>Commercial</li><li>Wood hood</li>
</ul>
<div class="scroll"><i></i></div>

<div class="cta"></div>
<div class="cta-text">Want to work with Us</div>
<div class="cta-btn">GET STARTED NOW</div>

<footer class="footer"></footer>
<div class="f-head" style="left:50px">ABOUT US</div>
<div class="f-head" style="left:272px">USEFUL LINKS</div>
<div class="f-head" style="left:420px">GET IN TOUCH</div>
<div class="f-head" style="left:627px">CONTACT</div>
<p class="f-text" style="left:50px;top:1018px;width:182px">At Bramblewood Joinery, we've been designing and manufacturing the Midwest's finest custom cabinets and fixtures since 1966. From single cabinets to room remodels to entire home installations, our expert artisans help turn the house you live in to the home you've always dreamed of.</p>
<span class="f-social" style="left:50px"></span><span class="f-social" style="left:68px"></span><span class="f-social" style="left:89px"></span><span class="f-social" style="left:111px"></span>
<ul class="f-links">
  <li>Home</li><li>Who We Are</li><li>Getting Started</li><li>Contact Us</li><li>Customer Experience</li><li>Professional</li><li>Portfolio</li><li>Cabinet Hardware</li>
</ul>
<p class="f-text f-green" style="left:420px;top:1017px;width:142px;font-size:8px">Doloreiur quia commolu ptatemp dolupta oreprerum</p>
<svg class="abs" style="left:421px;top:1046px" width="6" height="8" viewBox="0 0 6 8"><path d="M3 0a3 3 0 0 0-3 3c0 2 3 5 3 5s3-3 3-5a3 3 0 0 0-3-3z" fill="#999"/></svg>
<p class="f-text" style="left:431px;top:1045px;width:120px">Bramblewood Joinery, Owen Hartley 1200 Orchard Lane, Fairview, ST 00000</p>
<svg class="abs" style="left:421px;top:1083px" width="6" height="8" viewBox="0 0 6 8"><rect x=".5" y=".5" width="5" height="7" rx="1" fill="none" stroke="#999"/></svg>
<p class="f-text" style="left:431px;top:1081px;font-size:8px">Phone :555.014.2300</p>
<svg class="abs" style="left:420px;top:1099px" width="7" height="6" viewBox="0 0 7 6"><rect x=".5" y=".5" width="6" height="5" fill="none" stroke="#999"/><path d="M.5 .5 3.5 3 6.5 .5" fill="none" stroke="#999"/></svg>
<p class="f-text" style="left:431px;top:1097px;font-size:8px">hello@bramblewoodjoinery.example</p>
<p class="f-text f-green" style="left:627px;top:1017px;width:128px;font-weight:600">Conecus iure posae volor remped modis</p>
<div class="f-field" style="top:1046px">Email</div>
<div class="f-field" style="top:1073px">Contact For<svg style="position:absolute;right:8px;top:7px" width="8" height="5"><path d="M0 0l4 4 4-4" stroke="#777" fill="none"/></svg></div>
<div class="btn btn-green" style="left:713px;top:1110px;width:55px;height:15px;font-size:7px">CONTACT</div>
<div class="copy">© 2015 bramblewoodjoinery.example. All rights reserved.</div>
</body>
</html>
```